Business card for a new cabinet shop company named Veloran Cabinets for high end cabinets

Design a business card, thinking dark rich green with colours to speak of high end luxury ie; cream, gold, black possibly

Mitchell Tarrowby
Director Craftsman
Email: info@veloranjoinery-example.com.au
Instagram : @veloran.cabinets

```html
<!DOCTYPE html>
<html lang="en">
<head>
<meta charset="utf-8">
<title>Veloran Cabinets – Business Card</title>
<link rel="stylesheet" href="https://fonts.googleapis.com/css2?family=Montserrat:wght@500;700&family=Poppins:wght@400&display=swap">
<style>
  :root {
    --backdrop: #1c3a2b;
    --forest: #1f4030;
    --gold: #cca95e;
    --gold-light: #d7bc80;
    --gold-mid: #d1b070;
    --white: #ffffff;
  }
  * { box-sizing: border-box; margin: 0; padding: 0; }
  html, body {
    width: 1200px;
    height: 1108px;
    overflow: hidden;
    background: var(--backdrop);
  }
  .card {
    position: absolute;
    left: 242px;
    width: 715px;
    height: 409px;
    border-radius: 36px;
  }
  .card-front {
    top: 119px;
    background: linear-gradient(118deg,
      var(--gold) 0%, var(--gold) 38%,
      var(--gold-light) 47%, var(--gold-mid) 62%,
      var(--gold) 100%);
    display: flex;
    align-items: center;
    justify-content: center;
    gap: 26px;
  }
  .brand-dot {
    width: 46px;
    height: 46px;
    border-radius: 50%;
    border: 4px solid var(--white);
    flex: none;
  }
  .brand-name {
    font-family: "Poppins", sans-serif;
    font-weight: 400;
    font-size: 58px;
    letter-spacing: 1px;
    color: var(--white);
    white-space: nowrap;
  }
  .card-back {
    top: 580px;
    background: var(--white);
    display: flex;
    align-items: center;
    justify-content: center;
  }
  .identity {
    text-align: right;
    padding-right: 18px;
  }
  .person-name {
    font-family: "Montserrat", sans-serif;
    font-weight: 700;
    font-size: 28px;
    color: var(--gold);
    white-space: nowrap;
    line-height: 1.1;
  }
  .person-role {
    font-family: "Montserrat", sans-serif;
    font-weight: 500;
    font-size: 17px;
    color: var(--forest);
    margin-top: 6px;
    white-space: nowrap;
  }
  .divider {
    width: 2px;
    height: 54px;
    background: var(--gold);
    flex: none;
  }
  .contacts {
    list-style: none;
    padding-left: 22px;
    font-family: "Montserrat", sans-serif;
    font-weight: 500;
    font-size: 17px;
    color: var(--forest);
  }
  .contacts li {
    display: flex;
    align-items: center;
    gap: 10px;
    white-space: nowrap;
    line-height: 1.6;
  }
  .contact-icon { flex: none; }
</style>
</head>
<body>
  <section class="card card-front" aria-label="Card front">
    <span class="brand-dot" aria-hidden="true"></span>
    <span class="brand-name">Veloran Cabinets</span>
  </section>

  <section class="card card-back" aria-label="Card back">
    <div class="identity">
      <p class="person-name">Mitchell Tarrowby</p>
      <p class="person-role">Director Craftsman</p>
    </div>
    <span class="divider" aria-hidden="true"></span>
    <ul class="contacts">
      <li>
        <svg class="contact-icon" width="15" height="11" viewBox="0 0 15 11" aria-hidden="true">
          <rect x="0" y="0" width="15" height="11" fill="#cca95e"/>
          <path d="M0 0 L7.5 6 L15 0" fill="none" stroke="#ffffff" stroke-width="1.4"/>
        </svg>
        info@veloranjoinery-example.com.au
      </li>
      <li>
        <svg class="contact-icon" width="15" height="15" viewBox="0 0 15 15" aria-hidden="true">
          <circle cx="7.5" cy="7.5" r="6.5" fill="none" stroke="#cca95e" stroke-width="1.6"/>
        </svg>
        @veloran.cabinets
      </li>
    </ul>
  </section>
</body>
</html>
```